Bold Flyer Needed for Bold Little Gym

We need a 1 page flyer created for our small boutique fitness facility, CorVanto, which highlights a new service we are offering.
We are now offering Red Light Therapy (RLT) to our members and I need a full color, 1 page flyer created that captures the eye of our members while highlighting the benefits and clearly stating the prices at the bottom of the page.
Flyer will be printed out on a standard 8.5" x 11" sheet of paper and should be laid out in a way that is easy to read. Landscape or Portrait layouts are both expectable.
We are using Silverline Glow Therapy Lights LumaCore 700 Lamps as found here http://lnk.example/7QWRT5Z
I have attached the text that should be included and our logo for branding of the flyer.
Thank you!

```html
<!DOCTYPE html>
<html lang="en">
<head>
<meta charset="utf-8">
<title>CorVanto Red Light Therapy Flyer</title>
<link href="https://fonts.googleapis.com/css2?family=Saira+Semi+Condensed:wght@600;700;800&family=Karla:wght@400;500;700&display=swap" rel="stylesheet">
<style>
  :root {
    --ink: #0b0a0c;
    --night: #1a1420;
    --yellow: #f9d10a;
    --red: #ef0a23;
    --white: #ffffff;
    --grey-text: #b9b9bd;
    --grey-line: #5a5a5e;
    --row-line: #2a2a2e;
  }
  * { margin: 0; padding: 0; box-sizing: border-box; }
  html, body { width: 927px; height: 1200px; overflow: hidden; background: var(--ink); }
  .flyer {
    position: relative; width: 927px; height: 1200px; overflow: hidden;
    background: var(--ink); color: var(--white);
    font-family: "Karla", Arial, sans-serif;
  }
  .display { font-family: "Saira Semi Condensed", "Arial Narrow", sans-serif; font-weight: 800; }
  .hero-night {
    position: absolute; left: 0; top: 0; width: 927px; height: 640px;
    background: linear-gradient(180deg, #120e16 0%, var(--night) 60%, #120e16 100%);
  }
  .hero-photo {
    position: absolute; left: 500px; top: 0; width: 427px; height: 560px;
    background: radial-gradient(ellipse at 55% 40%, #d3123a 0%, #8a1240 35%, #3a1a48 70%, var(--night) 100%);
  }
  .swooshes { position: absolute; left: 0; top: 0; }
  .logo {
    position: absolute; left: 103px; top: 14px;
    font-family: "Saira Semi Condensed", sans-serif; font-weight: 800;
    font-size: 54px; color: var(--yellow); letter-spacing: 0.5px;
  }
  .abs { position: absolute; }
  .headline { left: 61px; top: 210px; font-size: 27px; line-height: 35px; letter-spacing: 0.3px; }
  .subhead { left: 61px; font-size: 16.5px; letter-spacing: 0.1px; }
  .section-title { left: 61px; top: 384px; font-size: 24px; }
  .intro {
    left: 62px; top: 430px; width: 392px;
    font-size: 13px; line-height: 22.2px; color: #e8e8ea;
  }
  .offer { left: 430px; top: 524px; width: 380px; text-align: center; }
  .offer .label { font-size: 14px; }
  .offer .deal { font-size: 19.5px; color: var(--yellow); margin-top: 6px; line-height: 22px; }
  .offer .regular { font-size: 10px; color: #cfcfd2; letter-spacing: 0.3px; }
  .offer .limited { font-size: 14px; margin-top: 12px; }
  .offer-note { left: 362px; top: 626px; font-size: 12.5px; color: var(--grey-text); white-space: nowrap; }
  .pill {
    position: absolute; height: 55px; background: var(--red);
    border-radius: 0 28px 28px 0; display: flex; align-items: center;
    font-size: 18.5px; letter-spacing: 0.2px;
  }
  .pill--benefits { left: 0; top: 670px; width: 325px; padding-left: 21px; }
  .pill--why { left: 464px; top: 667px; width: 377px; padding-left: 45px; }
  .divider { position: absolute; left: 462px; top: 667px; width: 2px; height: 405px; background: var(--grey-line); }
  .feature { position: absolute; display: flex; gap: 11px; }
  .feature .icon {
    flex: none; width: 42px; height: 42px; border-radius: 50%;
    background: var(--yellow); display: flex; align-items: center; justify-content: center;
  }
  .feature .icon svg { width: 24px; height: 24px; fill: none; stroke: var(--ink); stroke-width: 1.6; stroke-linecap: round; stroke-linejoin: round; }
  .feature h3 { font-family: "Karla", sans-serif; font-weight: 700; font-size: 12.8px; letter-spacing: 0.4px; line-height: 16px; margin-top: 1px; }
  .feature p { font-size: 12.5px; color: var(--grey-text); line-height: 16px; margin-top: 4px; }
  .feature--why .text { width: 350px; }
  .prices {
    position: absolute; left: 508px; top: 967px; width: 398px;
    border-collapse: collapse; border: 1px solid var(--row-line);
    font-size: 11px;
  }
  .prices th { background: #151517; text-align: left; font-weight: 700; font-size: 14px; height: 37px; padding-left: 17px; }
  .prices td { height: 33px; padding-left: 17px; border-top: 1px solid var(--row-line); color: #e6e6e8; }
  .prices th:nth-child(1), .prices td:nth-child(1) { width: 124px; }
  .prices th:nth-child(2), .prices td:nth-child(2) { width: 155px; }
  .cta-band { position: absolute; left: 0; top: 0; }
  .cta { left: 30px; top: 1128px; width: 376px; text-align: center; color: var(--ink); }
  .cta h4 { font-size: 14.5px; }
  .cta p { font-size: 11px; line-height: 16px; margin-top: 8px; }
  .cta .phone { font-family: "Karla", sans-serif; font-weight: 700; font-size: 14.5px; }
  .tagline { left: 470px; top: 1168px; width: 440px; text-align: center; font-family: "Karla", sans-serif; font-weight: 700; font-size: 14.5px; }
</style>
</head>
<body>
<main class="flyer">
  <div class="hero-night"></div>
  <div class="hero-photo" role="img" aria-label="Client relaxing beside a red light therapy panel glowing red in a dim room"></div>

  <svg class="swooshes" width="927" height="700" viewBox="0 0 927 700" aria-hidden="true">
    <path d="M0 0 H540 C520 60 480 95 420 104 H0 Z" fill="var(--ink)"/>
    <path d="M540 0 C520 60 480 95 420 104 L452 98 C500 80 530 40 540 0 Z" fill="var(--yellow)"/>
    <path d="M0 145 C90 120 180 106 310 104 C170 112 60 170 0 236 Z" fill="var(--yellow)"/>
    <path d="M0 545 C60 590 200 620 420 557 C250 640 80 645 0 605 Z" fill="var(--yellow)"/>
    <path d="M0 605 C80 645 250 640 420 557 C260 652 80 660 0 640 Z" fill="var(--grey-line)"/>
    <path d="M480 515 C560 470 660 455 760 470 C850 485 900 505 927 525 V560 C870 520 780 490 680 490 C600 490 540 500 480 515 Z" fill="var(--yellow)"/>
    <path d="M480 515 C560 495 640 488 700 492 C800 500 880 560 927 660 V700 H480 Z" fill="var(--ink)"/>
    <path d="M500 510 C600 485 700 485 780 505 C850 525 900 580 927 640 V660 C890 590 820 520 720 505 C640 495 560 500 500 510 Z" fill="var(--grey-line)"/>
    <path d="M780 505 C850 525 900 580 927 620 V560 C890 530 840 505 780 505 Z" fill="var(--yellow)"/>
  </svg>

  <div class="logo">CorVanto</div>

  <h1 class="abs display headline">UNLOCK YOUR POTENTIAL WITH RED<br>LIGHT THERAPY AT CORVANTO!</h1>
  <p class="abs display subhead" style="top:294px">INTRODUCING OUR NEW RED LIGHT THERAPY ROOM!</p>
  <p class="abs display subhead" style="top:331px">TRANSFORM YOUR WELLNESS ROUTINE WITH THE POWER OF LIGHT!</p>
  <h2 class="abs display section-title">WHAT IS RED LIGHT THERAPY?</h2>
  <p class="abs intro">Red Light Therapy (RLT) is a revolutionary treatment that uses specific wavelengths of light to promote healing, reduce inflammation, and enhance overall well-being. At CorVanto, we are excited to offer the advanced Silverline Glow Therapy LumaCore 700 panels—designed to maximize your health benefits in a relaxing environment.</p>

  <div class="abs offer">
    <p class="display label">SPECIAL INTRODUCTORY OFFER!</p>
    <p class="display deal">TRY YOUR FIRST SESSION FOR JUST $25!</p>
    <p class="regular">(REGULARLY $55)</p>
    <p class="display limited">LIMITED TIME ONLY!</p>
  </div>
  <p class="abs offer-note">Book your session today and discover how Red Light Therapy can elevate your fitness journey</p>

  <div class="pill pill--benefits display">BENEFITS OF RED LIGHT THERAPY</div>
  <div class="pill pill--why display">WHY CHOOSE CORVANTO?</div>
  <div class="divider"></div>

  <div class="feature" style="left:23px;top:750px">
    <div class="icon"><svg viewBox="0 0 24 24"><circle cx="12" cy="12" r="9"/><path d="M13 5 L8 13 H12 L11 19 L16 11 H12 Z"/></svg></div>
    <div class="text"><h3>BOOSTS ENERGY LEVELS</h3><p>Feel revitalized and more energetic after each session.</p></div>
  </div>
  <div class="feature" style="left:23px;top:807px">
    <div class="icon"><svg viewBox="0 0 24 24"><path d="M4 19 C4 12 7 8 10 6 L12 9 L9 11 C12 12 15 12 17 14 C19 16 18 19 15 19 Z"/><circle cx="18" cy="7" r="2"/></svg></div>
    <div class="text"><h3>ENHANCES MUSCLE RECOVERY</h3><p>Speed up recovery times post-workout and reduce soreness.</p></div>
  </div>
  <div class="feature" style="left:23px;top:863px">
    <div class="icon"><svg viewBox="0 0 24 24"><path d="M12 3 L13.5 8 L18 9 L13.5 10.5 L12 15 L10.5 10.5 L6 9 L10.5 8 Z"/><path d="M4 17 H20 M4 20 H20"/></svg></div>
    <div class="text"><h3>IMPROVES SKIN HEALTH</h3><p>Reduce wrinkles, blemishes, and promote a youthful glow.</p></div>
  </div>
  <div class="feature" style="left:23px;top:920px">
    <div class="icon"><svg viewBox="0 0 24 24"><path d="M10 3 V9 C8 10 8 14 10 15 V21 M14 3 V9 C16 10 16 14 14 15 V21"/><path d="M6 12 H8 M16 12 H18"/></svg></div>
    <div class="text"><h3>SUPPORTS JOINT HEALTH</h3><p>Alleviate pain and inflammation, making movement easier</p></div>
  </div>
  <div class="feature" style="left:23px;top:977px">
    <div class="icon"><svg viewBox="0 0 24 24"><path d="M16 4 A7 7 0 1 0 20 15 A6 6 0 0 1 16 4 Z"/><path d="M17 6 H20 L17 9 H20"/></svg></div>
    <div class="text"><h3>PROMOTES BETTER SLEEP</h3><p>Improve your sleep patterns and overall restfulness.</p></div>
  </div>
  <div class="feature" style="left:23px;top:1033px">
    <div class="icon"><svg viewBox="0 0 24 24"><path d="M12 6 C9 10 8 12 8 14 A4 4 0 0 0 16 14 C16 12 15 10 12 6 Z"/><path d="M4 12 A8 8 0 0 1 12 4 M20 12 A8 8 0 0 1 12 20"/></svg></div>
    <div class="text"><h3>INCREASES CIRCULATION</h3><p>Enhance blood flow for better nutrient delivery to muscles.</p></div>
  </div>

  <div class="feature feature--why" style="left:508px;top:747px">
    <div class="icon"><svg viewBox="0 0 24 24"><rect x="4" y="5" width="16" height="10" rx="1"/><path d="M8 8 H9 M12 8 H13 M16 8 H17 M8 11 H9 M12 11 H13 M16 11 H17 M12 15 V20 M9 20 H15"/></svg></div>
    <div class="text"><h3>STATE-OF-THE-ART EQUIPMENT</h3><p>Experience the power of eight Silverline Glow Therapy LumaCore 700 panels—some of the best on the market!</p></div>
  </div>
  <div class="feature feature--why" style="left:508px;top:820px">
    <div class="icon"><svg viewBox="0 0 24 24"><rect x="6" y="4" width="12" height="17" rx="1"/><path d="M9 4 V3 H15 V4 M9 10 L11 12 L15 8 M9 16 H15"/></svg></div>
    <div class="text"><h3>EXPERT GUIDANCE</h3><p>Our trained staff will guide you through each session to ensure you get the most out of your therapy.</p></div>
  </div>
  <div class="feature feature--why" style="left:508px;top:893px">
    <div class="icon"><svg viewBox="0 0 24 24"><circle cx="12" cy="12" r="2.5"/><circle cx="5" cy="5" r="2"/><circle cx="19" cy="5" r="2"/><circle cx="5" cy="19" r="2"/><circle cx="19" cy="19" r="2"/><path d="M7 7 L10 10 M17 7 L14 10 M7 17 L10 14 M17 17 L14 14"/></svg></div>
    <div class="text"><h3>COMMUNITY FOCUSED</h3><p>Join a supportive community that prioritizes health and wellness.</p></div>
  </div>

  <table class="prices">
    <thead><tr><th>PRICES</th><th>CorVanto Member</th><th>Non-Member</th></tr></thead>
    <tbody>
      <tr><td>Single Session</td><td>$35</td><td>$55</td></tr>
      <tr><td>3 – Pack</td><td>$102</td><td>$159</td></tr>
      <tr><td>5 – Pack</td><td>$167</td><td>$259</td></tr>
      <tr><td>10 – Pack</td><td>$316</td><td>$491</td></tr>
    </tbody>
  </table>

  <svg class="cta-band" width="927" height="1200" viewBox="0 0 927 1200" aria-hidden="true">
    <path d="M0 1117 H410 L451 1200 H0 Z" fill="var(--yellow)"/>
    <path d="M430 1160 H927 V1200 H451 Z" fill="var(--red)"/>
  </svg>
  <div class="abs cta">
    <h4 class="display">READY TO SHINE?</h4>
    <p>Visit our front desk or call us at <span class="phone">(555) 214-8830</span> to schedule<br>your appointment.</p>
  </div>
  <p class="abs tagline">CorVanto Fitness Facility, Your Wellness, Our Commitment!</p>
</main>
</body>
</html>
```